A-Stand Directional Sign Design

Objective:
We need a professional graphic design for an A-Stand sign that will guide customers arriving in our parking lot to our office. The design should be visually clear, welcoming, and aligned with our brand identity.
REQUIREMENTS:
Two versions of the design:
- One with an arrow pointing left
- One with an arrow pointing right
(This allows us to place the A-Stand anywhere and flip the graphic as needed.)
DIMENSIONS:
- Viewable Area: 30" x 40"
BRAND ALIGNMENT:
- Colors, fonts, and overall style should match our website: www.glidemarrow.com
- Clean, modern, and professional look consistent with our aviation/tourism brand
CONTENT:
- Clear directional arrow (left or right depending on version)
- Text: “Office Entrance” or similar concise wording (designers may propose alternatives if they improve clarity)
READABILITY:
- Bold, high-contrast design for visibility from a distance
- Simple layout that avoids clutter
DELIVERABLES:
- Final artwork in print-ready format (PDF preferred)
- Two versions: Arrow Left and Arrow Right
DESIGN GOAL:
Ensure customers can easily find our office upon arrival, while reinforcing glideMARROW’s professional and welcoming brand image.
Target Market(s)
Tourism
Look and feel

```html
<!DOCTYPE html>
<html lang="en">
<head>
<meta charset="utf-8">
<title>glideMARROW – Office Entrance A-Stand Signs</title>
<link href="https://fonts.googleapis.com/css2?family=Michroma&display=swap" rel="stylesheet">
<style>
  :root {
    --page-bg: #ffffff;
    --sign-black: #121212;
    --sign-white: #ffffff;
    --brand-blue: #3f78b5;
    --sky-light: #dff0f3;
    --sky-top: #8fcad6;
    --sky-mid: #3f93a8;
    --sea: #5c9fb0;
    --shade-dark: #23292c;
    --shade-warm: #5a3a30;
    --cabin-ceiling: #d9cfc1;
    --cabin-light: #f1eeea;
    --cabin-mid: #8e8376;
    --cabin-teal: #3f4f55;
    --cabin-dark: #2a2a2a;
  }
  * { box-sizing: border-box; margin: 0; padding: 0; }
  html, body {
    width: 1043px;
    height: 1200px;
    overflow: hidden;
    background: var(--page-bg);
  }
  .canvas {
    position: relative;
    width: 1043px;
    height: 1200px;
  }
  .sign {
    position: absolute;
    top: 306px;
    width: 440px;
    height: 587px;
    overflow: hidden;
    background: var(--sign-black);
    font-family: "Michroma", sans-serif;
    color: var(--sign-white);
  }
  .sign--left  { left: 52px; }
  .sign--right { left: 552px; }

  .sign__photo {
    position: absolute;
    top: 0; left: 0;
    width: 100%;
    height: 300px;
  }
  .sign__photo--flight {
    background:
      radial-gradient(ellipse 70px 160px at 4% 55%, var(--shade-warm) 0%, rgba(90,58,48,0) 100%),
      radial-gradient(ellipse 110px 190px at 95% 70%, var(--shade-dark) 0%, rgba(35,41,44,0) 100%),
      radial-gradient(ellipse 130px 60px at 68% 18%, var(--sky-light) 0%, rgba(223,240,243,0) 100%),
      radial-gradient(ellipse 150px 70px at 50% 88%, var(--shade-dark) 0%, rgba(35,41,44,0) 100%),
      linear-gradient(180deg, var(--sky-top) 0%, var(--sky-mid) 45%, var(--sea) 62%, var(--sky-mid) 100%);
  }
  .sign__photo--cabin {
    background:
      radial-gradient(ellipse 110px 150px at 88% 55%, var(--cabin-light) 0%, rgba(241,238,234,0) 100%),
      radial-gradient(ellipse 130px 150px at 45% 78%, var(--cabin-teal) 0%, rgba(63,79,85,0) 100%),
      radial-gradient(ellipse 80px 140px at 8% 60%, var(--cabin-light) 0%, rgba(241,238,234,0) 100%),
      radial-gradient(ellipse 70px 120px at 98% 85%, var(--cabin-dark) 0%, rgba(42,42,42,0) 100%),
      linear-gradient(180deg, var(--cabin-ceiling) 0%, var(--cabin-mid) 55%, var(--cabin-dark) 100%);
  }
  .sign__panel {
    position: absolute;
    top: 0; left: 0;
    width: 100%;
    height: 100%;
  }
  .sign__panel path { fill: var(--sign-black); }

  .sign__message {
    position: absolute;
    top: 330px;
    text-transform: uppercase;
    line-height: 1;
  }
  .sign--left  .sign__message { left: 37px; width: 366px; }
  .sign--right .sign__message { left: 46px; width: 368px; }
  .sign__line {
    display: flex;
    align-items: center;
    font-size: 46px;
    height: 65px;
    white-space: nowrap;
    letter-spacing: -1px;
  }
  .sign__line--office { justify-content: space-between; }
  .sign__line--entrance { justify-content: center; }
  .arrow { flex: 0 0 auto; width: 100px; height: 30px; }
  .arrow path { fill: none; stroke: var(--sign-white); stroke-width: 6; stroke-linecap: round; stroke-linejoin: round; }

  .brand {
    position: absolute;
    left: 0;
    width: 100%;
    top: 525px;
    display: flex;
    justify-content: center;
    align-items: center;
    gap: 12px;
  }
  .brand__dot {
    width: 30px;
    height: 30px;
    border-radius: 50%;
    background: var(--brand-blue);
  }
  .brand__name {
    font-family: "Michroma", sans-serif;
    font-size: 22px;
    color: var(--brand-blue);
  }
</style>
</head>
<body>
<main class="canvas">

  <section class="sign sign--left" aria-label="Office entrance sign, arrow pointing left">
    <div class="sign__photo sign__photo--flight" role="img" aria-label="Photo of a pilot and passenger in a helicopter cockpit flying over a coastal city"></div>
    <svg class="sign__panel" viewBox="0 0 440 587" preserveAspectRatio="none" aria-hidden="true">
      <path d="M0,587 V255 C0,228 20,219 51,219 H80 C106,219 110,293 136,293 H440 V587 Z"/>
    </svg>
    <div class="sign__message">
      <div class="sign__line sign__line--office">
        <svg class="arrow" viewBox="0 0 100 30" aria-hidden="true"><path d="M96,15 H6 M18,4 L5,15 L18,26"/></svg>
        <span>Office</span>
      </div>
      <div class="sign__line sign__line--entrance">Entrance</div>
    </div>
    <div class="brand">
      <span class="brand__dot" aria-hidden="true"></span>
      <span class="brand__name">glideMARROW</span>
    </div>
  </section>

  <section class="sign sign--right" aria-label="Office entrance sign, arrow pointing right">
    <div class="sign__photo sign__photo--cabin" role="img" aria-label="Photo of smiling passengers wearing headsets inside a helicopter cabin"></div>
    <svg class="sign__panel" viewBox="0 0 440 587" preserveAspectRatio="none" aria-hidden="true">
      <path d="M0,587 V262 C0,238 18,226 48,226 H66 C92,226 96,293 122,293 H338 C364,293 368,222 396,222 C426,222 440,240 440,262 V587 Z"/>
    </svg>
    <div class="sign__message">
      <div class="sign__line sign__line--office">
        <span>Office</span>
        <svg class="arrow" viewBox="0 0 100 30" aria-hidden="true"><path d="M4,15 H94 M82,4 L95,15 L82,26"/></svg>
      </div>
      <div class="sign__line sign__line--entrance">Entrance</div>
    </div>
    <div class="brand">
      <span class="brand__dot" aria-hidden="true"></span>
      <span class="brand__name">glideMARROW</span>
    </div>
  </section>

</main>
</body>
</html>
```